Signage Design Project

Busisness is a bakery and deli long time owned by the Tavel family. Want to develop a new outside sign that communicates it is a deli and a bakery but keeps the tavel name in the design.

The sign when produced will be about 10' by 3' . It is not lighted at present but could be if it were advantageous.

The name of the store is:

Tavel's Harbor Lane Bakery and Deli. The concept is to have a new,modern sign that reinforces that it is a deli and a bakery, as most people only know about the bakery side of the business
Updates

The name Tavel is just a reinforcer so the people kno it is still in the family.  The emphasis should be on the HARBOR LANE BAKERY and DELI

Target Market(s)

Small business breakfast and lunch customers

Industry/Entity Type

Bakery

Requirements
Must have
• Great impact from the road. Communicate that it is a deli and a bakery. Keep the Tavel name but need not be a major design element

```html
<!DOCTYPE html>
<html lang="en">
<head>
<meta charset="utf-8">
<title>Tavel's Harbor Lane Bakery and Deli – Storefront Sign</title>
<link rel="stylesheet" href="https://fonts.googleapis.com/css2?family=Niconne&family=Righteous&display=swap">
<style>
  :root {
    --sign-brown: #a87f55;
    --flourish-brown: #9a7249;
    --sign-gold: #ffc60a;
    --shadow-dark: #2b1a0c;
  }
  html, body {
    margin: 0;
    padding: 0;
    overflow: hidden;
    background: var(--sign-brown);
  }
  .sign {
    position: relative;
    width: 1200px;
    height: 360px;
    background: var(--sign-brown);
    overflow: hidden;
  }
  .flourish {
    position: absolute;
    top: 12px;
    width: 66px;
    height: 336px;
    background: linear-gradient(180deg, var(--sign-brown), var(--flourish-brown) 50%, var(--sign-brown));
    border-radius: 33px;
  }
  .flourish--left { left: 12px; }
  .flourish--right { right: 12px; }
  .sign-lettering {
    position: absolute;
    inset: 0;
    width: 1200px;
    height: 360px;
  }
  .family-name {
    font-family: "Niconne", cursive;
    font-size: 70px;
    fill: var(--sign-gold);
    filter: drop-shadow(2px 2px 0 var(--shadow-dark));
  }
  .business-type {
    font-family: "Righteous", sans-serif;
    font-size: 128px;
    fill: var(--sign-gold);
    filter: drop-shadow(4px 3px 0 var(--shadow-dark));
  }
</style>
</head>
<body>
  <div class="sign">
    <div class="flourish flourish--left" role="img" aria-label="Decorative scrolling swirl ornament running down the left edge"></div>
    <div class="flourish flourish--right" role="img" aria-label="Decorative scrolling swirl ornament running down the right edge"></div>

    <svg class="sign-lettering" viewBox="0 0 1200 360" xmlns="http://www.w3.org/2000/svg">
      <text class="family-name" x="600" y="140" text-anchor="middle" textLength="540" lengthAdjust="spacingAndGlyphs">Tavel's Harbor Lane</text>
      <text class="business-type" x="600" y="282" text-anchor="middle" textLength="1030" lengthAdjust="spacingAndGlyphs">Bakery and Deli</text>
    </svg>
  </div>
</body>
</html>
```